Help design website for "Brightwater Civic Advisors" to advance the common good

Here is the Google doc link that lays out the design:

https://files.plumrivet.example/sheet/d/7QmTzR2wLx9KpVbN4hJcY8sEaUoFdG3iXkMnPq5rWt6/edit?usp=sharing

Here is the Google drive folder with the logos and photos: https://vault.plumrivet.example/open?id=4HkWp9LzQe2TxRvN8mBaYc3DsUoJfG6

The testimonials are being gathered and will be shared by Friday, 1/4.

The winner will also have to migrate the coding files to my hosting site.

Thank you for your help! Looking forward to seeing your designs.

Target Market(s)

Prospective clients

Industry/Entity Type

Non Profit

Coding

Coded - Design and coding required

Number of Pages Required

5+ page

Requirements
Must have
• Noted in the Google doc regarding layout.
Nice to have

```html
<!DOCTYPE html>
<html lang="en">
<head>
<meta charset="utf-8">
<title>Brightwater Civic Advisors — Articles</title>
<link rel="stylesheet" href="https://fonts.googleapis.com/css2?family=Montserrat:wght@500;600;700;800&family=Open+Sans:wght@400;600&display=swap">
<style>
:root{
  --navy:#1d2735;
  --navy-deep:#161e2a;
  --blue:#2f7fc8;
  --blue-dark:#256aa9;
  --ink:#2a2f36;
  --muted:#5d646d;
  --paper:#ffffff;
  --wash:#f3f4f6;
  --line:#e1e4e8;
}
*{box-sizing:border-box;margin:0;padding:0}
html,body{width:1200px;height:3000px;overflow:hidden;background:var(--paper)}
body{font-family:"Open Sans",Arial,sans-serif;color:var(--ink)}
.site-header{height:90px;background:var(--navy);display:flex;align-items:center;justify-content:space-between;padding:0 120px}
.brand{display:flex;align-items:center;gap:14px;color:#fff;font-family:"Montserrat",Arial,sans-serif;font-weight:700;font-size:17px;letter-spacing:3px;text-transform:uppercase;line-height:1.2}
.brand-mark{width:30px;height:30px;border:2px solid #fff}
.header-right{display:flex;flex-direction:column;align-items:flex-end;gap:12px}
.cta-outline{border:1.5px solid #fff;color:#fff;font-family:"Montserrat",Arial,sans-serif;font-weight:600;font-size:10px;letter-spacing:1px;text-transform:uppercase;padding:6px 14px}
.main-nav{display:flex;gap:26px;color:#fff;font-family:"Montserrat",Arial,sans-serif;font-weight:600;font-size:11px;letter-spacing:1px;text-transform:uppercase}
.hero{position:relative;height:420px;background:linear-gradient(180deg,#c9cdd1 0%,#9aa0a6 45%,#5b5f63 100%)}
.hero svg{position:absolute;left:0;bottom:0}
.articles-intro{text-align:center;padding:44px 0 36px}
.articles-intro h1{font-family:"Montserrat",Arial,sans-serif;font-weight:800;font-size:40px;color:var(--ink)}
.articles-intro p{margin-top:8px;font-size:15px;color:var(--muted)}
.article-grid{width:920px;margin:0 auto;display:grid;grid-template-columns:1fr 1fr;gap:36px 40px}
.article-card{height:930px;background:var(--paper);box-shadow:0 2px 10px rgba(0,0,0,.12);display:flex;flex-direction:column}
.card-photo{position:relative;height:340px}
.card-caption{position:absolute;left:0;right:0;bottom:0;background:rgba(20,26,36,.82);color:#fff;font-family:"Montserrat",Arial,sans-serif;font-weight:700;font-size:13px;letter-spacing:.5px;text-transform:uppercase;line-height:1.45;padding:16px 22px}
.card-body{padding:30px 26px;flex:1;display:flex;flex-direction:column}
.card-body h2{font-family:"Montserrat",Arial,sans-serif;font-weight:700;font-size:20px;line-height:1.3;margin-bottom:16px}
.card-body p{font-size:13.5px;line-height:1.72;color:var(--muted);margin-bottom:14px}
.btn{display:inline-block;background:var(--blue);color:#fff;font-family:"Montserrat",Arial,sans-serif;font-weight:700;font-size:11px;letter-spacing:1px;text-transform:uppercase;padding:11px 20px;align-self:flex-start}
.view-all{text-align:center;margin-top:52px}
.view-all .btn{padding:13px 26px}
.site-footer{position:absolute;left:0;right:0;top:2720px;height:280px;background:var(--navy-deep)}
.footer-band{height:6px;background:var(--blue)}
.footer-inner{display:flex;justify-content:space-between;padding:64px 120px 0}
.footer-brand{display:flex;align-items:center;gap:18px;color:#fff;font-family:"Montserrat",Arial,sans-serif;font-weight:700;font-size:26px;letter-spacing:5px;text-transform:uppercase;line-height:1.2}
.footer-brand .brand-mark{width:44px;height:44px}
.footer-tag{margin-top:10px;color:#aeb6c2;font-size:11px;letter-spacing:2px;text-transform:uppercase}
.footer-menu h3{color:#fff;font-family:"Montserrat",Arial,sans-serif;font-size:11px;font-weight:700;letter-spacing:1px;text-transform:uppercase;margin-bottom:14px}
.footer-menu ul{list-style:none;display:flex;gap:22px;color:#c5ccd6;font-size:11px;text-transform:uppercase;letter-spacing:1px}
.footer-menu small{display:block;margin-top:16px;color:#8a93a0;font-size:10px}
</style>
</head>
<body>
<header class="site-header">
  <div class="brand"><span class="brand-mark"></span><span>Brightwater<br>Civic Advisors</span></div>
  <div class="header-right">
    <span class="cta-outline">Book a complimentary consultation</span>
    <nav class="main-nav"><span>About</span><span>Services &amp; Testimonials</span><span>Media &amp; Impact</span><span>Contact</span></nav>
  </div>
</header>

<section class="hero" role="img" aria-label="Photo of community members walking together along a city street">
  <svg width="1200" height="60" viewBox="0 0 1200 60" aria-hidden="true">
    <path d="M0 30 Q600 -10 1200 30 L1200 60 L0 60 Z" fill="#ffffff"/>
    <path d="M0 30 Q600 -10 1200 30 L1200 42 Q600 2 0 42 Z" fill="#2f7fc8"/>
  </svg>
</section>

<main>
  <div class="articles-intro">
    <h1>Articles</h1>
    <p>Media coverage for the programs and events that Nadia oversees.</p>
  </div>

  <div class="article-grid">
    <article class="article-card">
      <div class="card-photo" role="img" aria-label="Photo of attendees listening to a speaker at a dinner dialogue" style="background:linear-gradient(160deg,#6b6258,#3a3430)">
        <div class="card-caption">Attendees listening to a speaker at the Lanternpoint dinner dialogue event</div>
      </div>
      <div class="card-body">
        <h2>Residents Meet With Employment Nonprofit</h2>
        <p>Students and South Side community members attended a "Dinner Dialogue" recently featuring the nonprofit Lanternpoint Works. Conversation centered around the work done by Lanternpoint to help residents break the cycle of poverty and unemployment.</p>
        <p>The Dinner Dialogue series, created by the university's Community Service Center in 2017, seeks to promote the discussion of social justice issues. The meals are hosted three times a quarter at different South Side partner organizations, and are open to the public.</p>
        <p>Four of the attendees included Dela Okafor, a program officer and graduate student at Lakeshore University, Marisol Trent, a Lanternpoint Works volunteer, and two university students who joined for the evening.</p>
        <span class="btn">Read more</span>
      </div>
    </article>

    <article class="article-card">
      <div class="card-photo" role="img" aria-label="Photo of students performing at an outdoor park arts festival" style="background:linear-gradient(160deg,#8fa0ad,#4d5a63)">
        <div class="card-caption">Students performing at the third annual Ashgrove Park arts festival</div>
      </div>
      <div class="card-body">
        <h2>Community and Student Arts Shine at Ashgrove Park</h2>
        <p>Every year it gets bigger and better, said the festival's lead organizer, describing the third annual Ashgrove Park Arts Festival that took place last Saturday. A collaboration between student government, the community service center, and several other partners.</p>
        <p>The festival featured artists of all ages from across the South Side, including student entrepreneurs, residents, and neighborhood groups, with a place to connect and showcase their artistic skills. The festival was held in the park's central field.</p>
        <p>Throughout the afternoon, vendors such as local bakers and makers provided food and goods for the event, while schoolkids ran around the grass, adding laughter and color to everyone's day.</p>
        <span class="btn">Read more</span>
      </div>
    </article>

    <article class="article-card">
      <div class="card-photo" role="img" aria-label="Photo of attendees seated at tables listening to a speaker" style="background:linear-gradient(160deg,#6b6258,#3a3430)">
        <div class="card-caption">Attendees listening to a speaker at the Lanternpoint dinner dialogue event</div>
      </div>
      <div class="card-body">
        <h2>Residents Meet With Employment Nonprofit</h2>
        <p>Students and South Side community members attended a "Dinner Dialogue" recently featuring the nonprofit Lanternpoint Works. Conversation centered around the work done by Lanternpoint to help residents break the cycle of poverty and unemployment.</p>
        <p>The Dinner Dialogue series, created by the university's Community Service Center in 2017, seeks to promote the discussion of social justice issues. The meals are hosted three times a quarter at different South Side partner organizations, and are open to the public.</p>
        <p>Four of the attendees included Dela Okafor, a program officer and graduate student at Lakeshore University, Marisol Trent, a Lanternpoint Works volunteer, and two university students who joined for the evening.</p>
        <span class="btn">Read more</span>
      </div>
    </article>

    <article class="article-card">
      <div class="card-photo" role="img" aria-label="Photo of a stage with a projected day of service banner" style="background:linear-gradient(160deg,#2e4a78,#1a2640)">
        <div class="card-caption">Students performing at the third annual Ashgrove Park arts festival</div>
      </div>
      <div class="card-body">
        <h2>Building the Beloved Community</h2>
        <p>Throughout his career as a civil rights activist, the leader honored each January pursued a tumultuous but deep-seated relationship with this city. In many ways, in our city, that struggle launched the fair housing movement as part of an initiative of local leadership councils to further engage northern urban areas in the fight for racial equality.</p>
        <p>He persisted despite violent opposition, and ultimately helped inspire the widespread activism that led to the Fair Housing Act. During this period of advocacy, he gave his first major address at a packed stadium and many later joined him in the following decades.</p>
        <p>This year, the university continued to honor that legacy with its annual day of service, held on January 14.</p>
        <span class="btn">Read more</span>
      </div>
    </article>
  </div>

  <div class="view-all"><span class="btn">View all articles</span></div>
</main>

<footer class="site-footer">
  <div class="footer-band"></div>
  <div class="footer-inner">
    <div>
      <div class="footer-brand"><span class="brand-mark"></span><span>Brightwater<br>Civic Advisors</span></div>
      <div class="footer-tag">Advancing the common good</div>
    </div>
    <div class="footer-menu">
      <h3>Menu</h3>
      <ul><li>About</li><li>Services &amp; Testimonials</li><li>Media &amp; Impact</li><li>Contact</li></ul>
      <small>Copyright © 2019 All Rights Reserved.</small>
    </div>
  </div>
</footer>
</body>
</html>
```